"Vine Hollow Excursions" is a top notch Santa Barbara County Wine Tour company.

We provide scenic, boutique and custom wine tours. I need the card to be clean and classy. I will provide our logo. I would like the logo to cover the back side of the card as an option and would like to see a couple color options other then our signature green and gold. I would like to see some creative options and let the designers come up with options.
I need cards for myself and my team. The final design should communicate "An authentic and boutique wine tour experience"
Please use my website for reference www.vinehollowexcursions.example

Target Market(s)

We have a wide range of clients from millennials to baby boomers

Industry/Entity Type

Tour

Contact Information for Business Card

Contact info:
Dale Morton
805-219-6384
info@vinehollowexcursions.example
vinehollowexcursions.example

Colors

Designer to choose colors to be used in the design.

Requirements
Must have
• my logo
Nice to have
• *I would like to have the backside side with the logo and the company statement
• "An authentic and boutique wine tour experience" as an option.
• *I would also like to see what the designers can create!
• *I would like to see an option that incorporates or social: instagram, yelp, trip advisor
Should not have
• I do not want it too busy.

```html
<!DOCTYPE html>
<html lang="en">
<head>
<meta charset="utf-8">
<title>Vine Hollow Excursions – Business Card</title>
<link rel="stylesheet" href="https://fonts.googleapis.com/css2?family=Open+Sans:wght@400;600;700&display=swap">
<style>
  :root {
    --backdrop: #e4e4e2;
    --card-dark: #111111;
    --card-light: #f4f4f2;
    --ink-light: #f2f2f2;
    --vine-green: #1e5b3a;
    --gold: #b59c7e;
    --gold-soft: #cdbba4;
    --shadow: rgba(0, 0, 0, 0.18);
  }
  * { box-sizing: border-box; margin: 0; padding: 0; }
  html, body {
    width: 1167px;
    height: 1200px;
    overflow: hidden;
    background: var(--backdrop);
    font-family: "Open Sans", Arial, sans-serif;
  }
  .sheet {
    width: 1167px;
    height: 1200px;
    display: flex;
    flex-direction: column;
    align-items: center;
    justify-content: center;
    gap: 60px;
  }
  .card {
    position: relative;
    width: 900px;
    height: 514px;
    border-radius: 4px;
    box-shadow: 0 10px 30px var(--shadow);
    overflow: hidden;
  }

  /* Back side */
  .card--back {
    background: var(--card-dark);
    display: flex;
    flex-direction: column;
    align-items: center;
    justify-content: center;
    gap: 34px;
  }
  .brand-name {
    font-weight: 600;
    letter-spacing: 0.06em;
    text-transform: uppercase;
    white-space: nowrap;
  }
  .card--back .brand-name {
    color: var(--ink-light);
    font-size: 40px;
  }
  .social-row {
    display: flex;
    align-items: center;
    gap: 14px;
  }
  .social-row .rule {
    width: 70px;
    height: 1px;
    background: var(--ink-light);
    opacity: 0.7;
  }
  .social-dot {
    width: 20px;
    height: 20px;
    border-radius: 50%;
    background: var(--ink-light);
  }

  /* Front side */
  .card--front {
    background: var(--card-light);
  }
  .front-brand {
    position: absolute;
    left: 40px;
    top: 0;
    width: 370px;
    height: 400px;
    display: flex;
    align-items: center;
    justify-content: center;
  }
  .card--front .brand-name {
    color: var(--gold);
    font-size: 25px;
  }
  .divider {
    position: absolute;
    left: 440px;
    top: 110px;
    width: 1px;
    height: 250px;
    background: linear-gradient(to bottom, transparent, var(--gold) 25%, var(--gold) 75%, transparent);
  }
  .contact {
    position: absolute;
    left: 480px;
    top: 120px;
  }
  .contact__name {
    color: var(--vine-green);
    font-size: 30px;
    font-weight: 700;
    margin-bottom: 26px;
  }
  .contact__list { list-style: none; }
  .contact__item {
    display: flex;
    align-items: center;
    gap: 14px;
    color: var(--gold);
    font-size: 19px;
    line-height: 1;
    margin-bottom: 16px;
  }
  .contact__item svg {
    width: 18px;
    height: 18px;
    flex: none;
    fill: var(--vine-green);
  }
  .tagline {
    position: absolute;
    left: 230px;
    right: 40px;
    bottom: 58px;
    display: flex;
    align-items: center;
    gap: 16px;
    color: var(--gold);
    font-size: 17px;
  }
  .tagline .rule {
    flex: 1;
    height: 1px;
    background: var(--vine-green);
    opacity: 0.6;
  }
</style>
</head>
<body>
<main class="sheet">

  <section class="card card--back" aria-label="Card back">
    <div class="brand-name">Vine Hollow Excursions</div>
    <div class="social-row" aria-label="Social profiles">
      <span class="rule"></span>
      <span class="social-dot"></span>
      <span class="social-dot"></span>
      <span class="social-dot"></span>
      <span class="social-dot"></span>
      <span class="rule"></span>
    </div>
  </section>

  <section class="card card--front" aria-label="Card front">
    <div class="front-brand">
      <div class="brand-name">Vine Hollow Excursions</div>
    </div>

    <div class="divider"></div>

    <div class="contact">
      <h1 class="contact__name">Dale Morton</h1>
      <ul class="contact__list">
        <li class="contact__item">
          <svg viewBox="0 0 24 24" aria-hidden="true"><path d="M6.6 10.8a15.1 15.1 0 0 0 6.6 6.6l2.2-2.2a1 1 0 0 1 1-.25 11.4 11.4 0 0 0 3.6.57 1 1 0 0 1 1 1V20a1 1 0 0 1-1 1A17 17 0 0 1 3 4a1 1 0 0 1 1-1h3.5a1 1 0 0 1 1 1c0 1.25.2 2.45.57 3.6a1 1 0 0 1-.25 1z"/></svg>
          805-219-6384
        </li>
        <li class="contact__item">
          <svg viewBox="0 0 24 24" aria-hidden="true"><path d="M2 5h20v14H2z M4 7v.5l8 5 8-5V7z" fill-rule="evenodd"/></svg>
          info@vinehollowexcursions.example
        </li>
        <li class="contact__item">
          <svg viewBox="0 0 24 24" aria-hidden="true"><path d="M12 2a10 10 0 1 0 0 20 10 10 0 0 0 0-20zm6.9 6h-3a15 15 0 0 0-1.3-3.9A8 8 0 0 1 18.9 8zM12 4c.8 1.1 1.5 2.5 1.9 4h-3.8c.4-1.5 1.1-2.9 1.9-4zM4.3 14a8 8 0 0 1 0-4h3.4a16 16 0 0 0 0 4zm.8 2h3a15 15 0 0 0 1.3 3.9A8 8 0 0 1 5.1 16zm3-8h-3a8 8 0 0 1 4.3-3.9A15 15 0 0 0 8.1 8zM12 20c-.8-1.1-1.5-2.5-1.9-4h3.8c-.4 1.5-1.1 2.9-1.9 4zm2.3-6H9.7a14 14 0 0 1 0-4h4.6a14 14 0 0 1 0 4zm.3 5.9a15 15 0 0 0 1.3-3.9h3a8 8 0 0 1-4.3 3.9zm1.7-5.9a16 16 0 0 0 0-4h3.4a8 8 0 0 1 0 4z"/></svg>
          www.vinehollowexcursions.example
        </li>
      </ul>
    </div>

    <p class="tagline">
      <span class="rule"></span>
      An authentic and boutique wine tour experience
      <span class="rule"></span>
    </p>
  </section>

</main>
</body>
</html>
```